Finding the Root: Reason in Clinical Choice-Crafting

I'd like a cover that looks like it would fit on the shelf next to "The Illness Mirage" by Corwin Talley, "The Close of Forgetting" by Hugh Marchetti, "Meal Mend" by Paul Grieve, "The Energy Restart Plan" by Oscar Pemberley or "The Gland Restart Plan" by the same or "The Cortex Restart Plan" by the same ... either text only (with some interesting fonts that make the title stand out, and the subtitle smaller) or a relevant image, though I'm not entirely sure what that would be since this is a book about big-picture medical decision making.
Author name is Dr Tessa Morrow, NMD
I'll eventually request an e-book, paperback, and audio cover from the winner...

Target Market(s)

practicing physicians

Industry/Entity Type

medicine

Requirements
Must have
• look similar to other books in the genre

```html
<!DOCTYPE html>
<html lang="en">
<head>
<meta charset="utf-8">
<title>Finding the Root – Book Cover</title>
<link rel="stylesheet" href="https://fonts.googleapis.com/css2?family=EB+Garamond:wght@400;500;600&display=swap">
<style>
  :root {
    --backdrop: #02060a;
    --paper: #f4f4f4;
    --ink: #0a0a0a;
    --ink-soft: #231f20;
    --leaf: #97bb3f;
    --maze-grey: #cfcfcf;
  }
  html, body {
    margin: 0;
    padding: 0;
    width: 1200px;
    height: 1200px;
    overflow: hidden;
    background: var(--backdrop);
  }
  .book-cover {
    display: block;
    width: 1200px;
    height: 1200px;
  }
  .cover-paper { fill: var(--paper); }
  .author-band { fill: var(--leaf); }
  .subtitle {
    font-family: "EB Garamond", serif;
    font-size: 38px;
    font-weight: 500;
    fill: var(--ink-soft);
  }
  .title-main {
    font-family: "EB Garamond", serif;
    font-weight: 500;
    fill: var(--ink);
  }
  .title-accent {
    font-family: "EB Garamond", serif;
    font-weight: 500;
    fill: var(--leaf);
  }
  .author-name {
    font-family: "EB Garamond", serif;
    font-size: 50px;
    font-weight: 500;
    fill: var(--ink);
  }
</style>
</head>
<body>
<svg class="book-cover" viewBox="0 0 1200 1200" xmlns="http://www.w3.org/2000/svg" aria-labelledby="cover-title">
  <title id="cover-title">Finding the Root: Reason in Clinical Choice-Crafting, by Dr Tessa Morrow, NMD</title>
  <defs>
    <linearGradient id="maze-fade-top" x1="0" y1="0" x2="0" y2="1">
      <stop offset="0" stop-color="#f1f1f1"/>
      <stop offset="1" stop-color="#d6d6d6"/>
    </linearGradient>
    <linearGradient id="maze-fade-bottom" x1="0" y1="0" x2="0" y2="1">
      <stop offset="0" stop-color="#d6d6d6"/>
      <stop offset="1" stop-color="#f1f1f1"/>
    </linearGradient>
  </defs>

  <rect class="cover-paper" x="273" y="109" width="654" height="982"/>

  <rect class="maze-panel maze-panel--top" x="361" y="126" width="477" height="120"
        fill="url(#maze-fade-top)" role="img" aria-label="Faint grey line maze pattern"/>

  <text class="subtitle" x="361" y="297" textLength="477" lengthAdjust="spacing">REASON IN CLINICAL</text>
  <text class="subtitle" x="361" y="340" textLength="477" lengthAdjust="spacing">CHOICE-CRAFTING</text>

  <rect class="maze-panel maze-panel--bottom" x="361" y="366" width="477" height="92"
        fill="url(#maze-fade-bottom)" role="img" aria-label="Grey line maze pattern with a green path leading to an exit arrow"/>

  <text class="title-main" x="316" y="607" font-size="190" textLength="568" lengthAdjust="spacingAndGlyphs">Finding</text>
  <text class="title-main" x="600" y="743" font-size="160" text-anchor="middle">the</text>
  <text class="title-accent" x="316" y="927" font-size="218" textLength="568" lengthAdjust="spacingAndGlyphs">ROOT</text>

  <rect class="author-band" x="273" y="977" width="654" height="114"/>
  <text class="author-name" x="316" y="1045" textLength="568" lengthAdjust="spacing">Dr Tessa Morrow, NMD</text>
</svg>
</body>
</html>
```